Construction Company

Design a clutter free business card, it can be double-sided utilizing the logo for VKM Ltd simple with all relevant contact information.

Please also a letterhead design to function for the purposes of invoicing, all mail requirements, with header to be distinctive while the footer ties page together and incorporates all necessary information.

For now, please use generic / dummy text and when a winner is selected, I will disclose the contact information.

Hi Designers! Please read the updated brief which includes the design of a business card and letterhead. Thank you!

```html
<!DOCTYPE html>
<html lang="en">
<head>
<meta charset="utf-8">
<title>VKM Ltd Business Card</title>
<link href="https://fonts.googleapis.com/css2?family=Montserrat:wght@400;500;700&display=swap" rel="stylesheet">
<style>
  :root {
    --backdrop: #2a2a2c;
    --brand-blue: #0a3296;
    --brand-blue-light: #1647c2;
    --brand-gold: #b8900f;
    --paper: #ffffff;
    --ink: #2e2e33;
    --muted: #55555c;
  }
  * { margin: 0; padding: 0; box-sizing: border-box; }
  html, body { width: 1200px; height: 881px; overflow: hidden; }
  body {
    background: var(--backdrop);
    font-family: "Montserrat", sans-serif;
    position: relative;
  }
  .card {
    position: absolute;
    width: 560px;
    height: 320px;
    border-radius: 14px;
    overflow: hidden;
    box-shadow: 0 10px 28px rgba(0,0,0,0.45);
  }
  /* Back side */
  .card-back {
    left: 320px; top: 70px;
    background: var(--brand-blue);
    display: flex; align-items: center; justify-content: center;
  }
  .card-back .brand-mark {
    font-weight: 700;
    font-size: 64px;
    color: var(--brand-blue-light);
    letter-spacing: 2px;
  }
  /* Front side */
  .card-front {
    left: 320px; top: 470px;
    background: var(--paper);
  }
  .front-logo {
    position: absolute; left: 32px; top: 36px;
    font-weight: 700; font-size: 38px;
    color: var(--brand-blue);
    letter-spacing: 1px;
  }
  .gold-tab {
    position: absolute; right: 0; top: 40px;
    width: 12px; height: 38px;
    background: var(--brand-gold);
  }
  .person {
    position: absolute; right: 34px; top: 42px;
    text-align: right;
  }
  .person-name {
    font-weight: 700; font-size: 21px;
    color: var(--brand-blue); letter-spacing: 1.5px;
  }
  .person-title {
    font-size: 14px; color: var(--muted); letter-spacing: 1px; margin-top: 2px;
  }
  .divider {
    position: absolute; left: 32px; right: 32px; top: 126px;
    height: 1px; background: var(--brand-blue);
  }
  .address {
    position: absolute; right: 34px; top: 146px;
    text-align: right; font-size: 14px; line-height: 1.45;
    color: var(--ink); letter-spacing: 0.8px;
  }
  .contacts {
    position: absolute; left: 32px; top: 150px;
    list-style: none; font-size: 15px; color: var(--ink);
    letter-spacing: 0.8px;
  }
  .contacts li { display: flex; align-items: center; gap: 10px; height: 24px; }
  .contacts svg { width: 13px; height: 13px; flex: none; }
  .wave { position: absolute; left: 0; bottom: 0; width: 560px; height: 120px; }
</style>
</head>
<body>

<section class="card card-back" aria-label="Card back">
  <div class="brand-mark">VKM Ltd</div>
</section>

<section class="card card-front" aria-label="Card front">
  <div class="front-logo">VKM Ltd</div>
  <span class="gold-tab"></span>
  <div class="person">
    <div class="person-name">DANIEL CARTER</div>
    <div class="person-title">Founder</div>
  </div>
  <div class="divider"></div>

  <ul class="contacts">
    <li>
      <svg viewBox="0 0 16 16"><path d="M4 1.5l2.3 2.8-1.3 1.6c.8 2 2.3 3.5 4.2 4.3l1.5-1.3 2.8 2.3-1.4 2.6C7 13.7 2.3 9 1.5 3z" fill="var(--brand-blue)"/></svg>
      (555) 214-7730
    </li>
    <li>
      <svg viewBox="0 0 16 16"><rect x="1.5" y="3.5" width="13" height="9" fill="none" stroke="var(--brand-blue)" stroke-width="1.5"/><path d="M1.5 3.5L8 9l6.5-5.5" fill="none" stroke="var(--brand-blue)" stroke-width="1.5"/></svg>
      info@vkmltd.com
    </li>
    <li>
      <svg viewBox="0 0 16 16" fill="none" stroke="var(--brand-blue)" stroke-width="1.3"><circle cx="8" cy="8" r="6.5"/><ellipse cx="8" cy="8" rx="3" ry="6.5"/><path d="M1.5 8h13M2.5 4.8h11M2.5 11.2h11"/></svg>
      www.vkmltd.com
    </li>
  </ul>

  <div class="address">2870 Harbor Lane<br>Riverton, DE 19720</div>

  <svg class="wave" viewBox="0 0 560 120" preserveAspectRatio="none" aria-hidden="true">
    <path d="M0 110 C160 112 260 85 360 50 C440 22 500 12 560 14 L560 120 L0 120 Z" fill="var(--brand-blue)"/>
    <path d="M20 104 C170 102 260 76 360 40 C440 14 500 4 548 6" fill="none" stroke="var(--brand-gold)" stroke-width="3"/>
  </svg>
</section>

</body>
</html>
```